Editable Flyer Layout for DAYBREAK TRANSIT

to come up with a flyer layout that has editable spots to change promotions from time to time. We are a courier company in Calgary Alberta. Our logos and color schemes can be viewed on our website www.sendtranvolo.com We are wanting something that fits with website but more of an edge on the print media side. Our website also feature our "Focus" page which will tell you about us and our practices. Please conside this when constructing flyer. We also have additional image files for you if needed.

Thanks !!!!
Updates

Some of these designs are great. Never expected to get so many different results. I will comment on potential designs once we have reviewed all and only after deadline. For now Thanks to all .....!!!!!

Thank you all for your submissions. Some have been eliminated. Those that have not I have sent message to you. The designs look great but need some minor changes. I have sent some suggestions and revert back to you. Please review the notes above on ad (promo) and the editable space.

Thanks Very Much !!!

Ned

Thank You all very much for your submissions. We will be choosing a candidate today. We love this service, you all did awesome.

Thanks
Ned

Target Market(s)

Commerical businesses shipping freight and courier packages.

Industry/Entity Type

It Company

Requirements
Must have
• Flyer must be free of copyright.

```html
<!DOCTYPE html>
<html lang="en">
<head>
<meta charset="utf-8">
<title>Daybreak Transit – Flyer</title>
<link rel="stylesheet" href="https://fonts.googleapis.com/css2?family=Questrial&family=Libre+Baskerville:wght@400;700&display=swap">
<style>
  :root{
    --backdrop:#2a2421;
    --paper:#dcd7c6;
    --brand-blue:#1f78b8;
    --brand-blue-dark:#155a8c;
    --ink:#1f78b8;
    --body-ink:#3d3d3d;
    --white:#ffffff;
    --photo-warm:#b9a68c;
    --photo-cool:#9fb3c4;
  }
  *{box-sizing:border-box;margin:0;padding:0}
  html,body{width:1200px;height:900px;overflow:hidden;background:var(--backdrop)}
  body{position:relative;font-family:"Questrial",sans-serif;color:var(--body-ink)}

  .flyer-page{position:absolute;top:235px;width:560px;height:430px;background:var(--paper);
    box-shadow:0 10px 30px rgba(0,0,0,.55);overflow:hidden}
  .flyer-page--front{left:30px}
  .flyer-page--back{left:610px}
  .band-layer{position:absolute;inset:0}

  .abs{position:absolute}
  .heading{color:var(--ink);font-size:11px;line-height:1}
  .heading strong{display:block;font-size:17px;font-weight:400}
  .body-copy{font-size:7.5px;line-height:1.25;color:var(--ink)}

  /* front */
  .corner-brand{left:22px;top:16px;color:var(--brand-blue);font-size:11px;letter-spacing:.5px}
  .corner-brand small{display:block;font-size:6.5px;color:var(--brand-blue-dark);letter-spacing:0}
  .welcome{left:26px;top:72px;width:120px}
  .welcome .heading{margin-top:8px}
  .pledge{left:215px;top:70px;width:120px}
  .pledge .body-copy{margin-top:6px}

  .zone-sign{left:408px;top:42px;width:130px;height:130px}
  .zone-sign__text{position:absolute;inset:0;display:flex;flex-direction:column;align-items:center;justify-content:center;
    color:var(--white);text-align:center;font-size:8.5px;line-height:1.2}
  .zone-sign__text b{font-weight:400;font-size:10.5px}
  .zone-sign__text span{font-size:5.5px}

  .band-title{left:40px;top:235px;transform:rotate(-6deg);transform-origin:left top;color:var(--white)}
  .band-title__name{font-size:44px;letter-spacing:1px;line-height:1}
  .band-title__tag{font-size:13px;margin-top:2px;margin-left:30px}
  .caution{left:372px;top:206px;transform:rotate(-6deg);transform-origin:left top;color:var(--white);text-align:center}
  .caution__word{font-family:"Libre Baskerville",serif;font-size:24px}
  .caution__line{font-family:"Libre Baskerville",serif;font-size:8px;letter-spacing:.3px}

  .contact{left:215px;top:345px;color:var(--ink)}
  .contact address{font-style:normal;font-size:8px;line-height:1.35;margin-top:6px;font-weight:700}

  /* back */
  .about{left:52px;top:92px}
  .photo{position:absolute;border:4px solid var(--white);box-shadow:0 3px 8px rgba(0,0,0,.35)}
  .photo--courier{left:62px;top:190px;width:72px;height:92px;background:linear-gradient(160deg,#eef0f2,var(--photo-warm))}
  .photo--van{left:118px;top:292px;width:104px;height:100px;transform:rotate(-12deg);background:linear-gradient(160deg,#e9ecef,var(--photo-cool))}

  .services{left:290px;top:22px;width:250px}
  .services .heading{text-align:center;margin-bottom:6px}
  .service-list{list-style:none}
  .service-list li{margin-bottom:3px;color:var(--body-ink)}
  .service-list h3{font-weight:400;font-size:10px;line-height:1.05;color:var(--body-ink)}
  .service-list p{font-size:6px;line-height:1.15}
</style>
</head>
<body>

<section class="flyer-page flyer-page--front" aria-label="Flyer front">
  <svg class="band-layer" viewBox="0 0 560 430" aria-hidden="true">
    <polygon points="0,250 560,190 560,268 0,330" fill="var(--brand-blue)"/>
    <polygon points="0,330 560,268 560,274 0,336" fill="var(--brand-blue-dark)" opacity=".5"/>
  </svg>

  <div class="abs corner-brand">DAYBREAK TRANSIT<small>www.sendtranvolo.com</small></div>

  <div class="abs welcome">
    <p class="body-copy">Look to us for a friendly, reliable shipping experience. No extra fees for rush service. We only have rush service!</p>
    <h2 class="heading"><strong>Welcome</strong>message</h2>
  </div>

  <div class="abs pledge">
    <h2 class="heading">the<strong>Daybreak</strong>pledge</h2>
    <p class="body-copy">Our guarantee is that your shipment will always arrive when stated.</p>
  </div>

  <div class="abs zone-sign">
    <svg viewBox="0 0 130 130" width="130" height="130" aria-hidden="true">
      <rect x="23" y="23" width="84" height="84" transform="rotate(45 65 65)" fill="var(--brand-blue)" stroke="var(--white)" stroke-width="3"/>
    </svg>
    <div class="zone-sign__text"><b>Shipping</b>DAYBREAK<br>TRANSIT<span>Toll Free 1.800.555.0142</span><b>Zone</b></div>
  </div>

  <div class="abs band-title">
    <div class="band-title__name">DAYBREAK</div>
    <div class="band-title__tag">delivered by morning, every route</div>
  </div>

  <div class="abs caution">
    <div class="caution__word">Caution</div>
    <div class="caution__line">EXPRESS SHIPPING IN EFFECT</div>
  </div>

  <div class="abs contact">
    <h2 class="heading">contact<strong>Us</strong></h2>
    <address>Daybreak Transit<br>410- 18 Harbour Lane N.E., Calgary, AB<br>T2X-0B0 Canada<br>Toll Free: 1.800.555.0142</address>
  </div>
</section>

<section class="flyer-page flyer-page--back" aria-label="Flyer back">
  <svg class="band-layer" viewBox="0 0 560 430" aria-hidden="true">
    <polygon points="0,314 560,272 560,318 0,360" fill="var(--brand-blue)"/>
    <polygon points="0,374 360,346 360,380 0,408" fill="var(--brand-blue)"/>
  </svg>

  <h2 class="abs heading about">about<strong>Us</strong></h2>
  <div class="photo photo--courier" role="img" aria-label="Photo of a courier holding a parcel"></div>
  <div class="photo photo--van" role="img" aria-label="Photo of a white delivery van"></div>

  <div class="abs services">
    <h2 class="heading">our<strong>Services</strong></h2>
    <ul class="service-list">
      <li><h3>our focus</h3><p>Our focus is on the commercial shipping customer</p></li>
      <li><h3>our expertise</h3><p>Our expertise is overnight courier service</p></li>
      <li><h3>our guarantee</h3><p>Our guarantee is that your shipment will always arrive when stated</p></li>
      <li><h3>our commitment</h3><p>Our commitment is friendly and reliable shipping experience</p></li>
      <li><h3>no extra fees</h3><p>No extra fees will be charged for rush service, we only have rush service</p></li>
      <li><h3>no package misplaced</h3><p>Every parcel is scanned and tracked from pickup to delivery.</p></li>
      <li><h3>traceable freight</h3><p>Traceable freight is a must and we have added GPS systems to every vehicle.</p></li>
      <li><h3>web based dispatch</h3><p>To make the easiest shipping experience, we are adding online booking and live tracking.</p></li>
      <li><h3>on site services</h3><p>We offer on site service to site locations. On site service is available to over 25 work plants and sites in the province.</p></li>
    </ul>
  </div>
</section>

</body>
</html>
```